Red Mesa Greenworks Summit needs a marketing flyer

We need a full page graphic for our upcoming Forum that can also be converted into a website "header" for social media, etc.: "Red Mesa Greenworks Summit - Shaping Change Across the Made Landscape"

INTRODUCTION:
During the first week of August 2022, Q-VarDT is presenting the Red Mesa Greenworks Summit - Shaping Change Across the Made Landscape.

One of the most exciting aspects of this conference will be the bringing together of multiple organizations including for-profits and nonprofits, K-12’s and higher education, cities and counties and other governmental agencies, as well as architects, engineers, and contractors to collaboratively present and discuss issues and ideas related to sustainability, with a Texas focus.

This event will be a catalyst for public and private project owners to holistically gather information and momentum as we bring the resources and vision needed to achieve the goal of zero carbon emissions from the built environment by 2040, and address water, green space and the natural environment, transportation, equity, and funding, among other topics.

```html
<!DOCTYPE html>
<html lang="en">
<head>
<meta charset="utf-8">
<title>Red Mesa Greenworks Summit – Flyer</title>
<link rel="stylesheet" href="https://fonts.googleapis.com/css2?family=Catamaran:wght@800;900&family=Baloo+2:wght@700&family=Poppins:wght@400;500;600&display=swap">
<style>
:root{
  --blue:#3d56a6;
  --blue-dark:#2f4590;
  --green:#7cb342;
  --green-dark:#6aa13a;
  --grey:#4a4a4a;
  --text:#222;
  --paper:#ffffff;
  --stage:#f1f1f1;
  --panel:#f0f0f0;
}
*{margin:0;padding:0;box-sizing:border-box}
html,body{width:1200px;height:3000px;overflow:hidden;background:var(--stage)}
.flyer{position:absolute;left:60px;top:779px;width:1080px;height:1442px;background:var(--paper);overflow:hidden;box-shadow:0 6px 24px rgba(0,0,0,.18);font-family:'Poppins',sans-serif;color:var(--text)}
.flyer-bg{position:absolute;inset:0}
.brand{position:absolute;left:0;width:1080px;top:38px;display:flex;justify-content:center;align-items:center;gap:18px}
.brand-dot{width:86px;height:86px;border-radius:50%;background:var(--blue)}
.brand-text{display:flex;flex-direction:column}
.brand-name{font-family:'Poppins',sans-serif;font-weight:500;font-size:50px;line-height:1;color:var(--grey)}
.brand-sub{font-family:'Poppins',sans-serif;font-weight:500;font-size:11.5px;color:var(--green);margin-top:8px}
.title{position:absolute;left:0;width:1080px;top:528px;text-align:center;color:#fff;font-family:'Catamaran',sans-serif;font-weight:900;line-height:.95;letter-spacing:-.5px}
.title .l1{font-size:78px;display:block}
.title .l2{font-size:88px;display:block}
.title .l3{font-size:104px;display:block}
.tagline{position:absolute;left:0;width:1080px;top:858px;text-align:center;font-family:'Baloo 2',sans-serif;font-weight:700;font-size:40px;color:var(--green)}
.date-box{position:absolute;left:79px;top:938px;height:68px;display:flex}
.date-label{background:var(--blue);color:#fff;border-radius:8px 0 0 8px;padding:6px 12px 0 16px;display:flex;align-items:center;gap:12px}
.date-label small{font-size:23px;line-height:1.1;font-weight:400}
.date-label b{font-family:'Poppins',sans-serif;font-weight:500;font-size:46px}
.date-year{background:var(--grey);color:#fff;border-left:4px solid #fff;border-radius:0 8px 8px 0;padding:0 12px;font-size:50px;font-weight:500;display:flex;align-items:center}
.intro{position:absolute;left:80px;top:1016px;width:560px;font-size:19px;font-weight:500;line-height:1.3}
.highlight{position:absolute;left:80px;top:1082px;width:560px;font-size:19px;font-weight:600;line-height:1.3;color:var(--blue)}
.audience{position:absolute;list-style:none;font-size:17px;line-height:1.25}
.audience li{position:relative;padding-left:27px;margin-bottom:20px}
.audience.col1{left:74px;width:270px;top:1180px}
.audience.col2{left:348px;width:280px;top:1170px}
.tick{position:absolute;left:0;top:3px;width:14px;height:14px}
.vision{position:absolute;left:658px;top:938px;width:343px;height:364px;border:2px solid var(--blue);border-radius:10px;background:var(--panel);overflow:hidden}
.vision-tab{position:absolute;left:0;top:0;bottom:0;width:78px;background:var(--green);border-radius:0 30px 30px 0}
.vision-eye{position:absolute;left:20px;top:62px}
.vision-word{position:absolute;left:10px;top:290px;transform:rotate(-90deg);transform-origin:left top;color:#fff;font-size:42px;font-weight:600;letter-spacing:1px}
.vision-lead{position:absolute;left:95px;top:20px;width:235px;font-size:17px;line-height:1.2}
.vision-lead span{color:var(--blue)}
.vision-list{position:absolute;left:93px;top:110px;width:232px;list-style:none;font-size:17px}
.vision-list li{position:relative;padding-left:38px;height:33.5px;line-height:32px;border-bottom:1px solid #d8d8d8}
.vision-list li:last-child{border-bottom:none}
.vision-list .tick{top:10px;left:2px}
.rule{position:absolute;left:68px;right:80px;top:1332px;height:2px;background:#cfcfcf}
.contacts{position:absolute;left:64px;top:1362px;width:944px;display:flex;justify-content:space-between;align-items:center;font-size:29px;font-weight:500;color:var(--grey);white-space:nowrap}
.contacts span{display:flex;align-items:center;gap:8px}
</style>
</head>
<body>
<main class="flyer">
  <svg class="flyer-bg" width="1080" height="1442" viewBox="0 0 1080 1442">
    <defs>
      <radialGradient id="forestGlow" cx="52%" cy="42%" r="70%">
        <stop offset="0" stop-color="#fbf6c8"/>
        <stop offset=".25" stop-color="#d6da5a"/>
        <stop offset=".6" stop-color="#6f9b2c"/>
        <stop offset="1" stop-color="#3a6318"/>
      </radialGradient>
    </defs>
    <rect class="hero-photo" role="img" aria-label="Photo of a glowing light bulb held up in a sunlit green forest with eco icons" x="0" y="0" width="1080" height="900" fill="url(#forestGlow)"/>
    <path d="M211 0 A330 170 0 0 0 869 0 Z" fill="#fff"/>
    <polygon points="0,540 170,720 0,880" fill="var(--green)"/>
    <polygon points="1080,540 910,720 1080,880" fill="var(--green)"/>
    <path d="M0,900 Q0,790 110,720 L540,650 L970,720 Q1080,790 1080,900 L1080,1442 L0,1442 Z" fill="#fff"/>
    <ellipse cx="537" cy="645" rx="458" ry="205" fill="var(--blue)"/>
    <polygon points="0,1320 88,1442 0,1442" fill="var(--green)"/>
    <polygon points="1080,1320 992,1442 1080,1442" fill="var(--green)"/>
  </svg>

  <header class="brand">
    <div class="brand-dot"></div>
    <div class="brand-text">
      <span class="brand-name">Q-VarDT</span>
      <span class="brand-sub">Institute for Quality in Varied Design Trades</span>
    </div>
  </header>

  <h1 class="title"><span class="l1">RED MESA</span><span class="l2">GREENWORKS</span><span class="l3">SUMMIT</span></h1>
  <p class="tagline">Shaping Change Across the Made Landscape</p>

  <div class="date-box">
    <div class="date-label"><small>During the<br>first week of</small><b>AUGUST</b></div>
    <div class="date-year">2022</div>
  </div>

  <p class="intro">Q-VarDT is presenting the Red Mesa Greenworks Summit Shaping Change Across the Made Landscape.</p>
  <p class="highlight">One of the most exciting aspects of this conference will be the bringing together of multiple organizations including for-</p>

  <ul class="audience col1">
    <li><svg class="tick" viewBox="0 0 14 14"><circle cx="7" cy="7" r="6" fill="none" stroke="var(--green)" stroke-width="1.5"/><path d="M4 7.2l2 2 4-4" fill="none" stroke="var(--green)" stroke-width="1.5"/></svg>Profits and nonprofits,</li>
    <li><svg class="tick" viewBox="0 0 14 14"><circle cx="7" cy="7" r="6" fill="none" stroke="var(--green)" stroke-width="1.5"/><path d="M4 7.2l2 2 4-4" fill="none" stroke="var(--green)" stroke-width="1.5"/></svg>K-12’s and higher education,</li>
    <li><svg class="tick" viewBox="0 0 14 14"><circle cx="7" cy="7" r="6" fill="none" stroke="var(--green)" stroke-width="1.5"/><path d="M4 7.2l2 2 4-4" fill="none" stroke="var(--green)" stroke-width="1.5"/></svg>Cities and counties and other governmental agencies,</li>
  </ul>
  <ul class="audience col2">
    <li><svg class="tick" viewBox="0 0 14 14"><circle cx="7" cy="7" r="6" fill="none" stroke="var(--green)" stroke-width="1.5"/><path d="M4 7.2l2 2 4-4" fill="none" stroke="var(--green)" stroke-width="1.5"/></svg>Architects &amp; engineers,</li>
    <li><svg class="tick" viewBox="0 0 14 14"><circle cx="7" cy="7" r="6" fill="none" stroke="var(--green)" stroke-width="1.5"/><path d="M4 7.2l2 2 4-4" fill="none" stroke="var(--green)" stroke-width="1.5"/></svg>Contractors to collaboratively present and discuss issues and ideas related to sustainability, with a Texas focus.</li>
  </ul>

  <aside class="vision">
    <div class="vision-tab">
      <svg class="vision-eye" width="40" height="34" viewBox="0 0 40 34"><path d="M2 18 Q20 2 38 18 Q20 32 2 18Z" fill="none" stroke="#fff" stroke-width="3"/><circle cx="20" cy="18" r="6" fill="#fff"/></svg>
      <span class="vision-word">VISION</span>
    </div>
    <p class="vision-lead">Achieve the goal of zero carbon emissions from the <span>built environment by 2040.</span></p>
    <ul class="vision-list">
      <li><svg class="tick" viewBox="0 0 14 14"><circle cx="7" cy="7" r="6" fill="none" stroke="var(--green)" stroke-width="1.5"/><path d="M4 7.2l2 2 4-4" fill="none" stroke="var(--green)" stroke-width="1.5"/></svg>Address water</li>
      <li><svg class="tick" viewBox="0 0 14 14"><circle cx="7" cy="7" r="6" fill="none" stroke="var(--green)" stroke-width="1.5"/><path d="M4 7.2l2 2 4-4" fill="none" stroke="var(--green)" stroke-width="1.5"/></svg>Green space and the</li>
      <li><svg class="tick" viewBox="0 0 14 14"><circle cx="7" cy="7" r="6" fill="none" stroke="var(--green)" stroke-width="1.5"/><path d="M4 7.2l2 2 4-4" fill="none" stroke="var(--green)" stroke-width="1.5"/></svg>Natural environment,</li>
      <li><svg class="tick" viewBox="0 0 14 14"><circle cx="7" cy="7" r="6" fill="none" stroke="var(--green)" stroke-width="1.5"/><path d="M4 7.2l2 2 4-4" fill="none" stroke="var(--green)" stroke-width="1.5"/></svg>Transportation,</li>
      <li><svg class="tick" viewBox="0 0 14 14"><circle cx="7" cy="7" r="6" fill="none" stroke="var(--green)" stroke-width="1.5"/><path d="M4 7.2l2 2 4-4" fill="none" stroke="var(--green)" stroke-width="1.5"/></svg>Equity,</li>
      <li><svg class="tick" viewBox="0 0 14 14"><circle cx="7" cy="7" r="6" fill="none" stroke="var(--green)" stroke-width="1.5"/><path d="M4 7.2l2 2 4-4" fill="none" stroke="var(--green)" stroke-width="1.5"/></svg>Funding,</li>
      <li><svg class="tick" viewBox="0 0 14 14"><circle cx="7" cy="7" r="6" fill="none" stroke="var(--green)" stroke-width="1.5"/><path d="M4 7.2l2 2 4-4" fill="none" stroke="var(--green)" stroke-width="1.5"/></svg>Among other topics.</li>
    </ul>
  </aside>

  <div class="rule"></div>
  <footer class="contacts">
    <span><svg width="24" height="24" viewBox="0 0 24 24"><path d="M6.6 10.8a15 15 0 0 0 6.6 6.6l2.2-2.2a1 1 0 0 1 1-.25 11.4 11.4 0 0 0 3.6.57 1 1 0 0 1 1 1V20a1 1 0 0 1-1 1A17 17 0 0 1 3 4a1 1 0 0 1 1-1h3.5a1 1 0 0 1 1 1c0 1.25.2 2.45.57 3.57a1 1 0 0 1-.25 1z" fill="var(--blue)"/></svg>2145550187</span>
    <span><svg width="22" height="18" viewBox="0 0 24 20"><rect x="1" y="2" width="22" height="16" rx="2" fill="var(--blue)"/><path d="M2 4l10 7 10-7" fill="none" stroke="#fff" stroke-width="1.6"/></svg>info@Q-VarDT.com</span>
    <span><svg width="24" height="24" viewBox="0 0 24 24"><circle cx="12" cy="12" r="10" fill="none" stroke="var(--blue)" stroke-width="2"/><ellipse cx="12" cy="12" rx="4.5" ry="10" fill="none" stroke="var(--blue)" stroke-width="1.6"/><path d="M2 12h20M4 7h16M4 17h16" stroke="var(--blue)" stroke-width="1.4"/></svg>www.Q-VarDT.com</span>
  </footer>
</main>
</body>
</html>
```